Frostvale Harborline LLC

we need a business card design

Industry/Entity Type

hvac

Contact Information for Business Card

my logo

Requirements
Must have
• my logo and same colors

```html
<!DOCTYPE html>
<html lang="en">
<head>
<meta charset="utf-8">
<title>Frostvale Harborline LLC – Business Card</title>
<link href="https://fonts.googleapis.com/css2?family=Lato:wght@400;700&display=swap" rel="stylesheet">
<style>
  :root {
    --brand-blue: #0f5aa6;
    --deep-blue: #0b4a8f;
    --name-blue: #0d3f86;
    --sun-yellow: #f8bd4f;
    --paper: #ffffff;
    --backdrop: #3a3b3d;
    --ink: #1d1d1f;
  }
  * { margin: 0; padding: 0; box-sizing: border-box; }
  html, body {
    width: 1200px; height: 900px; overflow: hidden;
    background: var(--backdrop);
    font-family: "Lato", Arial, sans-serif;
  }
  .canvas {
    width: 1200px; height: 900px;
    display: flex; flex-direction: column; align-items: center; justify-content: center;
    gap: 44px;
  }
  .card {
    position: relative;
    width: 680px; height: 388px;
    border-radius: 30px;
    overflow: hidden;
  }
  /* Back side */
  .card-back {
    background: var(--brand-blue);
    display: flex; align-items: center; justify-content: center;
  }
  .brand-mark {
    display: flex; align-items: center; gap: 16px;
    font-weight: 700; font-size: 34px; color: var(--paper);
  }
  .brand-dot {
    width: 30px; height: 30px; border-radius: 50%;
    background: var(--sun-yellow);
  }
  /* Front side */
  .card-front { background: var(--paper); }
  .card-front .wave { position: absolute; inset: 0; width: 100%; height: 100%; }
  .front-brand {
    position: absolute; left: 56px; top: 140px;
    display: flex; align-items: center; gap: 12px;
    font-weight: 700; font-size: 25px; color: var(--brand-blue);
  }
  .front-brand .brand-dot { width: 22px; height: 22px; flex-shrink: 0; background: var(--brand-blue); }
  .holder {
    position: absolute; right: 44px; top: 30px; text-align: right;
  }
  .holder-name { font-size: 26px; font-weight: 700; color: var(--name-blue); }
  .holder-role { font-size: 15px; color: var(--ink); margin-top: 2px; }
  .edge-tab {
    position: absolute; right: 0; top: 26px;
    width: 16px; height: 36px; background: var(--deep-blue);
  }
  .contact-list {
    position: absolute; right: 28px; top: 170px;
    list-style: none; text-align: right;
    color: var(--paper); font-size: 14px; line-height: 25px;
  }
  .contact-list li { display: flex; align-items: center; justify-content: flex-end; gap: 10px; }
  .contact-list svg { width: 14px; height: 14px; flex-shrink: 0; }
  .contact-list .no-icon { padding-right: 24px; }
</style>
</head>
<body>
<main class="canvas">
  <section class="card card-back" aria-label="Card back">
    <div class="brand-mark"><span class="brand-dot"></span>Frostvale Harborline LLC</div>
  </section>

  <section class="card card-front" aria-label="Card front">
    <svg class="wave" viewBox="0 0 680 388" preserveAspectRatio="none" aria-hidden="true">
      <path class="wave-main" d="M680 95 C545 95 475 140 435 210 C395 290 355 360 260 388 L680 388 Z" fill="var(--brand-blue)"/>
      <path class="wave-swoosh" d="M525 100 C455 125 420 175 390 235 C350 315 305 360 190 386 C300 365 345 305 380 230 C415 160 455 120 525 100 Z" fill="var(--brand-blue)"/>
      <path class="wave-gold" d="M0 315 C130 300 260 280 320 215 C300 275 220 320 0 338 Z" fill="var(--sun-yellow)"/>
      <path class="wave-base" d="M0 358 C90 356 170 352 230 388 L0 388 Z" fill="var(--brand-blue)"/>
    </svg>
    <div class="edge-tab"></div>
    <div class="holder">
      <div class="holder-name">Marcus Ellery</div>
      <div class="holder-role">Owner</div>
    </div>
    <div class="front-brand"><span class="brand-dot"></span>Frostvale Harborline LLC</div>
    <ul class="contact-list">
      <li>044-123 456 789
        <svg viewBox="0 0 16 16"><path d="M3 1.5l3 3-1.5 2c1 2 2.5 3.5 4.5 4.5l2-1.5 3 3-2 2C6 14 2 10 1.5 3.5z" fill="#fff"/></svg></li>
      <li>info@frostvaleharbor.com
        <svg viewBox="0 0 16 16"><rect x="1" y="3" width="14" height="10" fill="#fff"/><path d="M1 3l7 6 7-6" stroke="var(--brand-blue)" stroke-width="1.5" fill="none"/></svg></li>
      <li>www.frostvaleharbor.com
        <svg viewBox="0 0 16 16"><circle cx="8" cy="8" r="6.5" fill="none" stroke="#fff" stroke-width="1.6"/><path d="M1.5 8h13M8 1.5c-3 3.5-3 9.5 0 13M8 1.5c3 3.5 3 9.5 0 13" stroke="#fff" stroke-width="1.2" fill="none"/></svg></li>
      <li>421, Address line goes here
        <svg viewBox="0 0 16 16"><path d="M8 15s-5-5.5-5-9a5 5 0 0110 0c0 3.5-5 9-5 9z" fill="#fff"/><circle cx="8" cy="6" r="1.8" fill="var(--brand-blue)"/></svg></li>
      <li class="no-icon">45452, Country name</li>
    </ul>
  </section>
</main>
</body>
</html>
```